Health and Wellbeing online Shop

I have attached a specification, however in summary this is a new business startup selling vitamins and supplements.

We need a web design for new wellbeing website, selling high end vitamins, supplements and nootropics. Therefore I need a simple eCommerce solution .

I need the website to look very different to other websites on the market. The more creative the better. It should look fresh elegant and simple. The criteria for products being on my site is that they have great reviews and they have been scientifically tested.

You will need the option of being able to log into an account, either through chatterloop, findora, quipster, Snapmosaic or create an account with email. For accounts, users will need the facility to reset passwords, see previous orders, track current order, and maintain favourites.

It should be PC, mobile and tablet friendly.

Look and Feel

It should be an elegant, modern, professional, trendy, unisex website. It should look clean and calm. Am happy to try interesting and slightly unusual designs. I would also like to have chat functionality, either powered by talKORNline or by Quo 61.

Websites I like are
https://www.plume-radiance.example.co.uk/
https://www.mereherbals.example.co.uk/
http://www.novadermis.example.com/

PLEASE DO USE YOUR KNOWELDGE OF WHAT WORKS FOR WEB DESIGN. YOU’RE THE EXPERT AND NEED YOUR EXPERTISE. CARTE BLANCHE TO DESIGN AS YOU SEE FIT. Please be creative, I need my site to stand out from the crowd.

Target Market(s)
Middle aged women are our most common client, however, younger patients, both male and female, will often visit the site. In summary, I would like the site to appeal to all age brackets.

Industry/Entity Type
Business

Coding
Coded - Design and coding required

Number of Pages Required
5 pages
Updates

I would like more designs. I was expecting 75+ Designs to choose from as per the package I paid for.

Target Market(s)

Industry/Entity Type

Health And Wellness

Coding

Number of Pages Required

5+ page

Requirements
Must have
• Creative design

```html
<!DOCTYPE html>
<html lang="en">
<head>
<meta charset="utf-8">
<title>Verdelle Clinic – Vitamins &amp; Skincare</title>
<link href="https://fonts.googleapis.com/css2?family=Cinzel:wght@400;500&family=Lato:wght@400;700&display=swap" rel="stylesheet">
<style>
:root{
  --gold:#c9a04f;
  --gold-dark:#b38c3f;
  --ink:#2f2f2f;
  --bar:#3a3a3a;
  --muted:#666;
  --line:#cfcfcf;
  --white:#fff;
  --hero:#7f979d;
  --side-head:#8c8c8c;
}
*{margin:0;padding:0;box-sizing:border-box}
html,body{width:1200px;height:4481px;overflow:hidden}
body{font-family:'Lato',sans-serif;color:var(--ink);background:var(--white);position:relative}
.serif{font-family:'Cinzel',serif}
section,header,footer,nav{position:absolute;left:0;width:1200px}
.abs{position:absolute}
.img{position:absolute}
.btn{position:absolute;display:flex;align-items:center;justify-content:center;font-family:'Lato',sans-serif;font-weight:700;font-size:12px;text-transform:uppercase;letter-spacing:.2px}
.btn-white{background:var(--white);color:var(--ink)}
.btn-gold{background:var(--gold);color:var(--white)}
/* top bar */
.topbar{top:0;height:42px;background:var(--bar);color:#fff;font-size:15px}
.topbar .welcome{left:174px;top:11px}
.social{display:flex;gap:7px}
.social span{width:20px;height:20px;border-radius:50%;background:var(--gold);display:block}
.topbar .social{position:absolute;left:870px;top:11px}
/* header */
.site-header{top:42px;height:118px}
.brand{position:absolute;left:172px;top:18px;display:flex;align-items:center;gap:10px}
.brand-mark{width:82px;height:82px;border-radius:50%;border:2px solid #555;display:block}
.brand-name{font-family:'Lato',sans-serif;font-size:14px;color:#555;letter-spacing:.5px;line-height:1.35}
.search{position:absolute;left:680px;top:35px;width:273px;height:52px;border:1.5px solid #555;display:flex}
.search span{flex:1;padding:15px 12px;font-size:14px;color:#555}
.search i{width:42px;margin:5px;background:var(--gold);display:flex;align-items:center;justify-content:center}
.cart{position:absolute;left:978px;top:38px}
.cart b{position:absolute;left:24px;top:-6px;width:22px;height:22px;border-radius:50%;background:var(--gold);color:#fff;font-size:13px;font-weight:400;display:flex;align-items:center;justify-content:center}
/* nav */
.main-nav{top:160px;height:57px;background:var(--gold)}
.main-nav ul{list-style:none;display:flex;position:absolute;left:221px;top:20px;gap:0}
.main-nav li{color:#fff;font-size:16px;margin-right:50px;text-transform:uppercase}
/* hero */
.hero{top:217px;height:646px}
.hero .img{inset:0;background:linear-gradient(90deg,#7b9399 0%,#8aa0a5 55%,#b9aea3 78%,#8a9ea2 100%)}
.hero h1{position:absolute;left:172px;top:130px;font-family:'Cinzel',serif;font-weight:500;font-size:60px;line-height:86px;color:#fff;letter-spacing:1px}
.dots{position:absolute;left:172px;top:440px;display:flex;gap:4px}
.dots span{width:16px;height:16px;border-radius:50%;background:#c9cfd1}
.dots span:first-child{background:#fff}
/* promos */
.promos{top:911px;height:752px}
.tile{position:absolute;overflow:hidden}
.tile .img{inset:0}
.tile h2{position:absolute;font-family:'Cinzel',serif;font-weight:400;line-height:1.25}
/* shop */
.shop{top:1732px;height:930px}
.sidebar{position:absolute;left:172px;top:0;width:207px;height:930px;border:2px solid #999}
.side-head{height:52px;background:var(--side-head);color:#fff;font-size:16px;display:flex;align-items:center;justify-content:space-between;padding:0 10px 0 12px;margin:2px}
.cat-list{list-style:none;margin:20px 0 0 24px}
.cat-list li{font-size:12.5px;line-height:25.6px;color:#333;position:relative;padding-left:18px}
.cat-list li::before{content:"›";position:absolute;left:0;top:0;color:var(--gold);font-size:15px}
.side-group{display:flex;justify-content:space-between;margin:0 16px 0 12px;font-weight:700;font-size:16px;color:#333;height:46px;align-items:center}
.featured-head{position:absolute;left:388px;top:0;width:640px;height:70px;background:var(--gold);color:#fff;font-size:21px;padding:24px 10px;text-transform:uppercase}
.filter{position:absolute;top:83px;height:48px;border:1.5px solid #555;font-size:13px;display:flex;align-items:center;justify-content:space-between;padding:0 8px}
.card{position:absolute;width:208px;height:380px;border:2px solid #aaa;text-align:center}
.card .img{left:0;top:0;width:204px;height:230px;border-bottom:1px solid #aaa}
.card .pname{position:absolute;left:0;right:0;top:258px;font-size:15px;text-transform:uppercase;color:#333}
.card .price{position:absolute;left:0;right:0;top:288px;font-size:14px;color:var(--gold)}
.card .btn{left:60px;top:314px;width:84px;height:42px;font-size:11px}
/* features */
.features{top:2749px;height:233px;background:var(--gold);color:#fff}
.feat{position:absolute;top:75px;display:flex;gap:14px}
.feat h3{font-weight:400;font-size:16px;text-transform:uppercase;margin-bottom:8px}
.feat p{font-size:15px;line-height:27px}
/* banner */
.banner{top:2982px;height:515px}
.banner .img{inset:0;background:linear-gradient(90deg,#c6e4ef 0%,#d7ecf2 45%,#dfe9ec 62%,#2f8a55 82%,#e9d0d0 100%)}
.banner .brand{left:172px;top:62px}
.banner h2{position:absolute;left:172px;top:218px;font-family:'Cinzel',serif;font-weight:400;font-size:42px;line-height:60px;color:#1d1d1d}
/* about */
.about{top:3497px;height:452px}
.about .img{left:0;top:0;width:520px;height:452px;background:linear-gradient(90deg,#c9a58e,#d8b7a0 60%,#efe6e0)}
.about h2{position:absolute;left:541px;top:58px;font-family:'Cinzel',serif;font-weight:400;font-size:36px;color:#1d1d1d}
.about p{position:absolute;left:541px;top:136px;width:487px;font-size:12.6px;line-height:27px;text-align:justify;color:#333}
/* newsletter */
.newsletter{top:3949px;height:98px;background:var(--bar);color:#fff}
.newsletter h3{position:absolute;left:179px;top:38px;font-weight:400;font-size:22px}
.newsletter .field{position:absolute;left:482px;top:21px;width:419px;height:56px;border:1.5px solid #ccc;font-size:12px;padding:21px 16px}
.newsletter .send{position:absolute;left:910px;top:21px;width:118px;height:56px;background:#fff;color:#222;font-size:14px;display:flex;align-items:center;justify-content:center}
/* footer */
.site-footer{top:4047px;height:434px}
.fcol{position:absolute;top:88px}
.fcol h4{font-weight:400;font-size:18px;margin-bottom:18px;text-transform:uppercase}
.fcol p,.fcol li{font-size:12.5px;line-height:22.5px;list-style:none;color:#333}
.fline{position:absolute;left:172px;top:342px;width:856px;height:1px;background:#555}
.copy{position:absolute;left:0;right:0;top:380px;text-align:center;font-size:13.5px}
.pay{width:144px;height:30px;border:1.5px solid #555;border-radius:4px;margin-top:22px;background:#eef1f6}
</style>
</head>
<body>

<header class="topbar">
  <span class="abs welcome">Welcome To Verdelle Clinic</span>
  <div class="social" aria-label="Social links"><span></span><span></span><span></span><span></span><span></span><span></span></div>
</header>

<header class="site-header">
  <div class="brand"><span class="brand-mark"></span><span class="brand-name">VERDELLE CLINIC</span></div>
  <div class="search"><span>Search</span><i><svg width="16" height="16" viewBox="0 0 16 16" fill="none" stroke="#fff" stroke-width="2"><circle cx="7" cy="7" r="4.5"/><path d="M10.5 10.5L14 14"/></svg></i></div>
  <div class="cart"><svg width="38" height="44" viewBox="0 0 38 44" fill="none" stroke="#333" stroke-width="2.4"><path d="M5 14h28l-3 26H8z"/><path d="M12 14c0-8 14-8 14 0"/></svg><b>0</b></div>
</header>

<nav class="main-nav">
  <ul><li>Home</li><li>Vitamins</li><li>Nootropics</li><li style="margin-right:45px">Contact Us</li><li>About Us</li><li>Skin Peels</li></ul>
</nav>

<section class="hero">
  <div class="img" role="img" aria-label="Smiling woman with a face mask holding a lemon slice over one eye"></div>
  <h1>Enhance<br>Enrich<br>Engage</h1>
  <div class="dots"><span></span><span></span><span></span></div>
</section>

<section class="promos">
  <div class="tile" style="left:172px;top:0;width:299px;height:369px">
    <div class="img" role="img" aria-label="Woman touching her cheek, anti-ageing skincare" style="background:linear-gradient(90deg,#8fa3a8,#a7b3b4 55%,#c9a88f)"></div>
    <h2 style="left:16px;top:20px;font-size:30px;color:#fff">Anti<br>Ageing</h2>
    <div class="btn btn-white" style="left:18px;top:120px;width:94px;height:50px">Shop Now</div>
  </div>
  <div class="tile" style="left:485px;top:0;width:543px;height:369px">
    <div class="img" role="img" aria-label="Smiling woman with hands on her face, skin lightening" style="background:linear-gradient(90deg,#8ea4aa,#9fb1b4 50%,#caa58a 75%,#9aaeb2)"></div>
    <h2 style="left:16px;top:28px;font-size:38px;color:#fff">Skin<br>Lightening</h2>
    <div class="btn btn-white" style="left:18px;top:156px;width:94px;height:50px">Shop Now</div>
  </div>
  <div class="tile" style="left:172px;top:383px;width:541px;height:369px">
    <div class="img" role="img" aria-label="Man touching his jaw, skin specialist treatment" style="background:linear-gradient(90deg,#d6d8dc,#dfe0e3 50%,#c6a690 75%,#d9dade)"></div>
    <h2 style="left:24px;top:50px;font-size:37px;color:#1d1d1d;line-height:60px">Skin Specialist<br>20% Off</h2>
    <div class="btn btn-gold" style="left:26px;top:188px;width:94px;height:50px">Shop Now</div>
  </div>
  <div class="tile" style="left:727px;top:383px;width:301px;height:369px">
    <div class="img" role="img" aria-label="Laughing man applying face cream" style="background:linear-gradient(90deg,#a2b2b6,#b9c2c3 50%,#c7a48c)"></div>
    <h2 style="left:24px;top:22px;font-size:32px;color:#1d1d1d;line-height:41px">Why<br>Choose<br>Us</h2>
    <div class="btn btn-gold" style="left:24px;top:166px;width:94px;height:48px">Shop Now</div>
  </div>
</section>

<section class="shop">
  <aside class="sidebar">
    <div class="side-head">CATEGORY <svg width="12" height="8" viewBox="0 0 12 8" fill="none" stroke="#fff" stroke-width="2"><path d="M1 1l5 5 5-5"/></svg></div>
    <ul class="cat-list">
      <li>Amino Acids,</li><li>Antioxidants</li><li>Cannabis Oil CBD</li><li>Chondroitin</li><li>Coenzyme Q10</li><li>Cod Liver Oil</li><li>Essential Fatty Acids</li><li>Evening Primrose Oils</li><li>Fish Oils</li><li>Glucosamine</li><li>Herbal / Botanical</li><li>Minerals</li><li>MultiVitamins</li><li>Omega-3</li><li>Pregnancy</li><li>Probiotics</li><li>Vegan</li><li>Vegetarian</li><li>Vitamin B</li><li>Vitamin C</li><li>Vitamin D</li><li>Vitamin E</li><li>Vitamin K</li>
    </ul>
    <div style="height:30px"></div>
    <div class="side-group">INTEREST <span>›</span></div>
    <div class="side-group">DELIVERY <span>›</span></div>
    <div class="side-group">NEW <span>›</span></div>
  </aside>

  <div class="featured-head">Featured Products</div>
  <div class="filter" style="left:388px;width:124px">Name <span>⌄</span></div>
  <div class="filter" style="left:522px;width:131px">Top Sellers <span>⌄</span></div>
  <div class="filter" style="left:663px;width:177px">Highest review score <span>⌄</span></div>
  <div class="filter" style="left:850px;width:178px">Price high to low <span>⌄</span></div>

  <div class="card" style="left:388px;top:153px"><div class="img" role="img" aria-label="Amber supplement bottle with promotional tag" style="background:linear-gradient(180deg,#fff,#f3ece6)"></div><p class="pname">Product Name</p><p class="price">28.75$ – 41.40$</p><div class="btn btn-gold">Shop Now</div></div>
  <div class="card" style="left:604px;top:153px"><div class="img" role="img" aria-label="Three white supplement jars" style="background:linear-gradient(180deg,#fff,#eef0f2)"></div><p class="pname">Skin Product</p><p class="price">28.75$ – 41.40$</p><div class="btn btn-gold">Shop Now</div></div>
  <div class="card" style="left:820px;top:153px"><div class="img" role="img" aria-label="Amber supplement bottle with promotional tag" style="background:linear-gradient(180deg,#fff,#f3ece6)"></div><p class="pname">Sample Product</p><p class="price">28.75$ – 41.40$</p><div class="btn btn-gold">Shop Now</div></div>
  <div class="card" style="left:388px;top:551px"><div class="img" role="img" aria-label="Amber supplement bottle with promotional tag" style="background:linear-gradient(180deg,#fff,#f3ece6)"></div><p class="pname">Product Name</p><p class="price">28.75$ – 41.40$</p><div class="btn btn-gold">Shop Now</div></div>
  <div class="card" style="left:604px;top:551px"><div class="img" role="img" aria-label="Three white supplement jars" style="background:linear-gradient(180deg,#fff,#eef0f2)"></div><p class="pname">Skin Product</p><p class="price">28.75$ – 41.40$</p><div class="btn btn-gold">Shop Now</div></div>
  <div class="card" style="left:820px;top:551px"><div class="img" role="img" aria-label="Amber supplement bottle with promotional tag" style="background:linear-gradient(180deg,#fff,#f3ece6)"></div><p class="pname">Sample Product</p><p class="price">28.75$ – 41.40$</p><div class="btn btn-gold">Shop Now</div></div>
</section>

<section class="features">
  <div class="feat" style="left:172px">
    <svg width="64" height="64" viewBox="0 0 64 64" fill="none" stroke="#fff" stroke-width="3"><path d="M52 20A24 24 0 1 0 54 40"/><path d="M52 8v12H40"/><path d="M38 24c-2-3-10-3-11 1s11 5 10 10-9 4-11 1M32 18v4M32 40v4"/></svg>
    <div><h3>Money Back Guarantee</h3><p>Returns &amp; Exchanges</p></div>
  </div>
  <div class="feat" style="left:490px">
    <svg width="80" height="54" viewBox="0 0 80 54" fill="none" stroke="#fff" stroke-width="3"><rect x="4" y="6" width="46" height="32"/><path d="M50 16h14l10 12v10H50"/><circle cx="18" cy="42" r="6"/><circle cx="62" cy="42" r="6"/></svg>
    <div><h3>Free Shipping</h3><p>On orders over $ 99.<br>This offer is valid on all<br>our store items.</p></div>
  </div>
  <div class="feat" style="left:784px">
    <svg width="56" height="56" viewBox="0 0 56 56" fill="none" stroke="#fff" stroke-width="3"><path d="M14 6l8 12-5 5c3 7 9 13 16 16l5-5 12 8-5 8C26 48 8 30 6 11z"/><path d="M32 8a16 16 0 0 1 16 16M32 16a8 8 0 0 1 8 8"/></svg>
    <div><h3>+44 1632 960418</h3><p>Monday – Friday: 8am<br>until 18:00pm</p></div>
  </div>
</section>

<section class="banner">
  <div class="img" role="img" aria-label="Woman with a green leaf beside her face on a pale blue background"></div>
  <div class="brand"><span class="brand-mark"></span><span class="brand-name" style="font-size:21px">VERDELLE CLINIC</span></div>
  <h2>Anti-Ageing Skin Care<br>20% Off</h2>
  <div class="btn btn-gold" style="left:172px;top:357px;width:104px;height:54px;font-size:14px">Shop Now</div>
</section>

<section class="about">
  <div class="img" role="img" aria-label="Profiles of three women of different ages"></div>
  <h2>About Verdelle Skin Clinic</h2>
  <p>Welcome to Verdelle Skin Clinic, leading supplier of skincare and beauty products. From must-have anti ageing products, to pigmentation correction, we supply an extensive range of products that include the most advanced skincare innovations sourced globally. Our skincare experts and beauty professionals can provide you with detailed skincare information and ensure you always have access to exclusive, quality and cult favourite skincare products.</p>
  <div class="btn btn-gold" style="left:541px;top:329px;width:103px;height:54px;font-size:14px">Shop Now</div>
</section>

<section class="newsletter">
  <h3>NEWSLETTER SIGN UP</h3>
  <div class="field">Please enter your email address</div>
  <div class="send">SEND NOW</div>
</section>

<footer class="site-footer">
  <div class="fcol" style="left:172px"><h4>Contact Us</h4><p>Orchard Court,<br>42 Linden Row,<br>London,<br>EC9Z 4QT.<br>+44 1632 960418<br>info@verdelleclinic.example.com</p></div>
  <div class="fcol" style="left:417px"><h4>Quick Links</h4><ul><li>Home</li><li>Shop All</li><li>Anti-Ageing</li><li>Collagen</li><li>Skin Lightening</li><li>Skin Peels</li><li>Contact us</li></ul></div>
  <div class="fcol" style="left:645px"><h4>Information</h4><ul><li>Shipping Informations</li><li>Return Policy</li><li>About us</li><li>Contact us</li><li>Terms &amp; Conditions</li><li>Privacy Policy</li></ul></div>
  <div class="fcol" style="left:871px"><h4>Follow Us</h4><div class="social"><span></span><span></span><span></span><span></span><span></span><span></span></div><div class="pay" role="img" aria-label="Accepted payment methods"></div></div>
  <div class="fline"></div>
  <p class="copy">Copyrights @ 2021 Verdelle SkinClinic. All Rights Reserved.</p>
</footer>

</body>
</html>
```